Professional and creative business card design for recruiting service providers

Our company supports German medium-sized companies in filling vacancies promptly. For this we use social media marketing and bring our customers into the visibility.

We want a professional but also creative design for our business cards.

Please look at lindqvar-staff.de to get an impression of our CI.

Target Market(s)

Small and medium-sized companies in Germany from the industry

Industry/Entity Type

Industrie, Handwerk

Contact Information for Business Card

Name, Position, Telefonnummer, Email, Website

Colors
EE7325
F08F49
F5BC92
FAE3D3
FDF4ED

Requirements
Must have
• A picture of the employee and in the style of www.lindqvar-staff.de

```html
<!DOCTYPE html>
<html lang="de">
<head>
<meta charset="utf-8">
<title>Lindqvar &amp; Staff – Visitenkarte</title>
<link rel="stylesheet" href="https://fonts.googleapis.com/css2?family=Jost:wght@500;600;700&family=Arimo:wght@400&display=swap">
<style>
  :root {
    --brand-orange: #EE7325;
    --card-orange: #F0612C;
    --card-black: #000000;
    --text-white: #FFFFFF;
    --page-bg: #ECEAE8;
    --ring-light: #F4F1F1;
    --ring-mid: #D9D3D4;
    --ring-dark: #BDB6B8;
  }
  * { box-sizing: border-box; margin: 0; padding: 0; }
  html, body {
    width: 1200px; height: 900px; overflow: hidden;
    background: var(--page-bg);
  }
  .business-card {
    position: absolute; left: 100px; top: 140px;
    width: 1000px; height: 620px;
    background: var(--card-black);
    overflow: hidden;
  }
  .accent-band {
    position: absolute; top: 0; right: 0;
    width: 321px; height: 100%;
    background: var(--card-orange);
  }
  .brand {
    position: absolute; left: 57px; top: 92px;
    display: flex; align-items: center; gap: 22px;
  }
  .brand-square {
    width: 86px; height: 86px;
    background: var(--brand-orange);
  }
  .brand-name {
    font-family: "Jost", sans-serif; font-weight: 700;
    font-size: 38px; line-height: 42px; letter-spacing: 3px;
    color: var(--text-white); text-transform: uppercase;
  }
  .person {
    position: absolute; left: 57px; top: 326px;
  }
  .person-name {
    font-family: "Jost", sans-serif; font-weight: 600;
    font-size: 38px; line-height: 44px;
    color: var(--brand-orange); text-transform: uppercase;
  }
  .person-role {
    font-family: "Arimo", sans-serif; font-weight: 400;
    font-size: 28px; line-height: 34px; color: var(--text-white);
  }
  .contact-list {
    position: absolute; left: 57px; top: 446px;
    list-style: none;
    font-family: "Arimo", sans-serif; font-size: 27px; color: var(--text-white);
  }
  .contact-item {
    display: flex; align-items: center; gap: 9px; height: 37px;
  }
  .contact-icon { width: 27px; height: 27px; flex: none; }
  .portrait-ring {
    position: absolute; left: 413px; top: 42px;
    width: 532px; height: 532px; border-radius: 50%;
    background: radial-gradient(circle at 35% 30%, var(--ring-light) 0%, var(--ring-mid) 60%, var(--ring-dark) 100%);
  }
  .portrait-photo {
    position: absolute; left: 56px; top: 56px;
    width: 420px; height: 420px; border-radius: 50%;
    border: 2px solid #111;
    background: linear-gradient(180deg, #E6E3E2 0%, #CFCBCA 45%, #2A2A2E 75%, #111114 100%);
  }
</style>
</head>
<body>
  <main class="business-card">
    <div class="accent-band"></div>

    <header class="brand">
      <div class="brand-square"></div>
      <div class="brand-name">Lindqvar<br>&amp; Staff</div>
    </header>

    <section class="person">
      <h1 class="person-name">Tobias Wendler</h1>
      <p class="person-role">Managing Director</p>
    </section>

    <ul class="contact-list">
      <li class="contact-item">
        <svg class="contact-icon" viewBox="0 0 24 24" aria-hidden="true"><path fill="#EE7325" d="M6.6 10.8a15.1 15.1 0 0 0 6.6 6.6l2.2-2.2c.3-.3.7-.4 1-.2 1.1.4 2.3.6 3.6.6.6 0 1 .4 1 1V20c0 .6-.4 1-1 1A17 17 0 0 1 3 4c0-.6.4-1 1-1h3.5c.6 0 1 .4 1 1 0 1.3.2 2.5.6 3.6.1.3 0 .7-.2 1z"/><path fill="none" stroke="#EE7325" stroke-width="1.8" d="M14 3.5a7 7 0 0 1 6.5 6.5M14 7a3.5 3.5 0 0 1 3 3"/></svg>
        <span>040-318 552 907</span>
      </li>
      <li class="contact-item">
        <svg class="contact-icon" viewBox="0 0 24 24" aria-hidden="true"><rect x="1.5" y="5" width="21" height="14" fill="#EE7325"/><path d="M1.5 5l10.5 8 10.5-8M1.5 19l8-7M22.5 19l-8-7" fill="none" stroke="#000" stroke-width="1.3"/></svg>
        <span>info@lindqvar-staff.de</span>
      </li>
      <li class="contact-item">
        <svg class="contact-icon" viewBox="0 0 24 24" aria-hidden="true"><circle cx="12" cy="12" r="11" fill="#EE7325"/><g fill="none" stroke="#000" stroke-width="1.2"><ellipse cx="12" cy="12" rx="4.5" ry="11"/><path d="M1 12h22M12 1v22M3 6.5h18M3 17.5h18"/></g></svg>
        <span>www.lindqvar-staff.de</span>
      </li>
    </ul>

    <div class="portrait-ring">
      <div class="portrait-photo" role="img" aria-label="Porträtfoto des Geschäftsführers im dunklen Sakko vor hellem Bürohintergrund"></div>
    </div>
  </main>
</body>
</html>
```